Online interactive tutorial for year 2 to year 12 students in Australia

Website design for a new online tutorial for year 2 to year 12 students in Australia.

- The tutorial will be conducted via live webcam and within a dedicated interactive space
- The tutorial will be provided by high scoring undergraduates studying in top Australian universities.
- The tutors will be going through interviews & assessments & only top students are allowed to apply.
- Parents will do search and select tutor and have short 15 mins video interaction with potential tutors before booking them for their children for tutoring.
- hourly cost of booking (no monthly subscription or no hour limits)
- Tutors will have their own profile

Please see the attached for detailed page functionality.

The look and feel of the design must consider the following:
- must be educational but not dull and should stand out
- must appeal to younger generation - tutees (8-18 years), tutors (19-25), parents (30-50).
- Ideas for Logos (brivora.com.au but not confirmed)

Target Market(s)

tutees (8-18 years), tutors (19-25 years), parents (30-50 years).

Industry/Entity Type

Education

Coding

Coded - Design and coding required

Number of Pages Required

5+ page

Font styles to use
Serif

Requirements
Must have
• The look and feel of the design must consider the following:
• - must be educational but not dull and should stand out
• - must appeal to younger generation - tutees (8-18 years), tutors (19-25), parents (30-50).
Should not have
• Dullness

```html
<!DOCTYPE html>
<html lang="en">
<head>
<meta charset="utf-8">
<title>Brivora – Online Training for Kids</title>
<link rel="stylesheet" href="https://fonts.googleapis.com/css2?family=Oswald:wght@400;500&family=Roboto:ital,wght@0,300;0,400;0,500;1,700&display=swap">
<style>
:root{
  --blue:#0a97dd;
  --blue-deep:#0a86c9;
  --ink:#2f2f2f;
  --text:#6f6f6f;
  --muted:#9a9a9a;
  --light:#f2f2f2;
  --white:#ffffff;
  --footer:#2e2e2e;
  --footer-text:#e4e4e4;
}
*{box-sizing:border-box;margin:0;padding:0}
html,body{width:1200px;height:2835px;overflow:hidden}
body{font-family:"Roboto",Arial,sans-serif;color:var(--text);background:var(--white);position:relative}
.wrap{width:1004px;margin:0 auto;position:relative}
.btn{display:inline-flex;align-items:center;justify-content:center;background:var(--blue);color:var(--white);font:500 15px "Roboto",Arial,sans-serif;text-transform:uppercase;letter-spacing:.3px}

/* header */
.site-header{height:87px}
.site-header .wrap{display:flex;align-items:center;justify-content:space-between;height:87px}
.brand{font:500 28px "Oswald",Arial,sans-serif;color:var(--blue);letter-spacing:.5px}
.main-nav{display:flex;gap:8px}
.main-nav a{font:400 12.5px "Roboto",Arial,sans-serif;color:#777;text-transform:uppercase;padding:9px 14px;text-decoration:none;letter-spacing:.3px}
.main-nav a.active{color:var(--blue);border:1px solid var(--blue)}

/* hero */
.hero{position:relative;height:593px;overflow:hidden}
.hero-photo{position:absolute;inset:0;background:linear-gradient(100deg,#6b4e3f 0%,#b58a6d 30%,#9a7060 55%,#c49b7e 75%,#5e4236 100%)}
.hero-shade{position:absolute;inset:0;background:rgba(0,0,0,.18)}
.hero-title{position:absolute;top:338px;left:0;right:0;text-align:center;font:400 41px/54px "Oswald",Arial,sans-serif;color:var(--white);text-transform:uppercase;text-shadow:0 2px 6px rgba(0,0,0,.3)}
.hero .btn{position:absolute;left:508px;top:465px;width:184px;height:56px;font-size:14px}
.hero-arrow{position:absolute;right:74px;top:240px}

/* welcome */
.welcome{background:var(--light);height:515px;padding-top:34px}
.section-title{text-align:center;font:400 25px "Roboto",Arial,sans-serif;color:var(--ink);text-transform:uppercase}
.section-lead{width:800px;margin:14px auto 0;text-align:center;font:300 12px/21px "Roboto",Arial,sans-serif;color:var(--muted)}
.audiences{display:flex;justify-content:space-between;margin-top:56px}
.audience{width:305px}
.audience-head{display:flex;align-items:center;gap:22px}
.audience-icon{width:78px;height:78px;border-radius:50%;border:1px solid #cfcfcf;background:var(--white);display:flex;align-items:center;justify-content:center}
.audience-icon.filled{background:var(--blue);border:6px solid #d9eefa}
.audience-name{font:400 17px "Roboto",Arial,sans-serif;color:var(--ink);text-transform:uppercase}
.audience-name span{text-transform:none}
.audience p{margin-top:20px;font:300 11.5px/20px "Roboto",Arial,sans-serif;color:#555}
.read-more{display:block;margin-top:14px;font:italic 700 10.5px "Roboto",Arial,sans-serif;color:#333;text-transform:uppercase}
.welcome .center{text-align:center;margin-top:62px}
.welcome .btn{width:228px;height:60px;font-size:16px}

/* student log-ins */
.logins{position:relative;height:293px;overflow:hidden}
.logins-photo{position:absolute;inset:0;background:linear-gradient(100deg,#3e2f29,#6b5245 40%,#4a3a33 70%,#2c221e)}
.logins-shade{position:absolute;inset:0;background:rgba(20,20,20,.45)}
.logins .wrap{padding-top:34px}
.logins .section-title{color:var(--white);font-weight:500}
.login-form{display:grid;grid-template-columns:repeat(3,311px);justify-content:space-between;row-gap:23px;margin-top:28px}
.field{height:60px;background:var(--white);font:300 11px "Roboto",Arial,sans-serif;color:#777;display:flex;align-items:center;padding-left:16px}
.login-form .btn{height:60px;font-size:13px}

/* services */
.services{height:544px;padding-top:38px}
.service-cards{display:flex;justify-content:space-between;margin-top:38px}
.service-card{width:330px;height:388px;border:1px solid #ddd;padding:15px 15px 0;text-align:center;box-shadow:0 12px 10px -8px rgba(0,0,0,.18);position:relative}
.service-photo{height:170px}
.service-card h3{margin-top:20px;font:400 16px "Roboto",Arial,sans-serif;color:var(--ink);text-transform:uppercase}
.service-card p{margin-top:16px;font:300 11.5px/20px "Roboto",Arial,sans-serif;color:#555}
.service-card .btn{position:absolute;left:50%;transform:translateX(-50%);bottom:0;width:110px;height:36px;font-size:12px}

/* how it works */
.how{height:402px;padding-top:60px}
.how .wrap{display:flex;gap:38px}
.video{width:464px;height:276px;border:2px solid #ddd;position:relative;background:linear-gradient(110deg,#5c4a3c,#a38166 45%,#d8b79b 75%,#8e6f5a)}
.play{position:absolute;left:50%;top:50%;width:46px;height:46px;margin:-23px 0 0 -23px;border-radius:50%;background:rgba(255,255,255,.85)}
.how-copy h2{font:400 25px "Roboto",Arial,sans-serif;color:var(--ink);text-transform:uppercase;margin-top:-2px}
.how-copy p{margin-top:22px;width:500px;font:300 11.5px/21px "Roboto",Arial,sans-serif;color:#555}
.how-copy .btn{margin-top:20px;width:166px;height:52px;font-size:15px}

/* footer */
.site-footer{background:var(--footer);height:337px;padding-top:38px;color:var(--footer-text)}
.subscribe{display:flex;align-items:center}
.subscribe h4{font:400 22px "Roboto",Arial,sans-serif;text-transform:uppercase;width:334px}
.subscribe .field{width:506px;height:42px;font-size:11px;color:#555}
.subscribe .btn{margin-left:8px;width:156px;height:42px;font-size:12px}
.footer-cols{display:flex;margin-top:48px}
.footer-col h5{font:400 15px "Roboto",Arial,sans-serif;text-transform:uppercase;margin-bottom:28px}
.footer-col ul{list-style:none}
.footer-col li{font:400 11.5px "Roboto",Arial,sans-serif;margin-bottom:13px;display:flex;align-items:center;gap:12px}
.bullet{width:0;height:0;border-left:6px solid var(--footer-text);border-top:4px solid transparent;border-bottom:4px solid transparent}
.col-links{width:247px}
.col-contact{width:322px}
.col-info{width:233px}
.col-follow p{width:200px;font:300 11.5px/18px "Roboto",Arial,sans-serif}
.socials{display:flex;gap:6px;margin-top:14px}
.socials span{width:38px;height:38px;border-radius:50%;border:2px solid var(--blue)}
.copyright{position:absolute;left:0;right:0;bottom:0;height:64px;background:var(--blue);color:var(--white);font:400 11px "Roboto",Arial,sans-serif;display:flex;align-items:center;justify-content:center}
</style>
</head>
<body>

<header class="site-header">
  <div class="wrap">
    <div class="brand">BRIVORA</div>
    <nav class="main-nav">
      <a class="active">Home</a><a>Courses</a><a>Events</a><a>Pages</a><a>Publications</a><a>Blog</a><a>Contact Us</a>
    </nav>
  </div>
</header>

<section class="hero">
  <div class="hero-photo" role="img" aria-label="Teacher and smiling children gathered around a laptop"></div>
  <div class="hero-shade"></div>
  <h1 class="hero-title">Online training website for kids<br>from 2 years to 12 years</h1>
  <a class="btn">Tutor Registration</a>
  <svg class="hero-arrow" width="20" height="50" viewBox="0 0 20 50"><path d="M3 2 L17 25 L3 48" fill="none" stroke="#fff" stroke-width="2" opacity=".8"/></svg>
</section>

<section class="welcome">
  <div class="wrap">
    <h2 class="section-title">Welcome to Brivora</h2>
    <p class="section-lead">There are many variations of passages of Lorem Ipsum available, but the majority have suffered alteration in some form, by injected humour, or randomised words which don't look even slightly believable. If you are going to use a passage of Lorem Ipsum, you need</p>
    <div class="audiences">
      <div class="audience">
        <div class="audience-head">
          <div class="audience-icon"><svg width="30" height="26" viewBox="0 0 30 26"><rect x="2" y="2" width="26" height="18" fill="none" stroke="#0a97dd" stroke-width="2"/><circle cx="11" cy="10" r="3" fill="#0a97dd"/><path d="M6 18 q5-6 10 0" fill="#0a97dd"/><path d="M10 24h10" stroke="#0a97dd" stroke-width="2"/></svg></div>
          <div class="audience-name">Tutees &nbsp;<span>(8-18 years)</span></div>
        </div>
        <p>There are many variations of passages of in Lorem Ipsum available, but the majority have suffered alteration in some form, by injected the humour, or randomised.</p>
        <a class="read-more">Read More</a>
      </div>
      <div class="audience">
        <div class="audience-head">
          <div class="audience-icon filled"><svg width="30" height="26" viewBox="0 0 30 26"><circle cx="11" cy="8" r="4" fill="#fff"/><path d="M3 22 q8-12 16 0z" fill="#fff"/><rect x="17" y="4" width="10" height="8" fill="none" stroke="#fff" stroke-width="2"/></svg></div>
          <div class="audience-name">Tutors &nbsp;<span>(19-25 )</span></div>
        </div>
        <p>There are many variations of passages of in Lorem Ipsum available, but the majority have suffered alteration in some form, by injected the humour, or randomised.</p>
        <a class="read-more">Read More</a>
      </div>
      <div class="audience">
        <div class="audience-head">
          <div class="audience-icon"><svg width="32" height="30" viewBox="0 0 32 30"><circle cx="8" cy="5" r="3.5" fill="#0a97dd"/><rect x="4" y="10" width="8" height="18" fill="#0a97dd"/><circle cx="24" cy="5" r="3.5" fill="#0a97dd"/><path d="M19 10h10l2 10h-14z" fill="#0a97dd"/><rect x="21" y="20" width="6" height="8" fill="#0a97dd"/><circle cx="16" cy="14" r="2.5" fill="#0a97dd"/><rect x="13.5" y="18" width="5" height="10" fill="#0a97dd"/></svg></div>
          <div class="audience-name">Parents &nbsp;<span>(30-50)</span></div>
        </div>
        <p>There are many variations of passages of in Lorem Ipsum available, but the majority have suffered alteration in some form, by injected the humour, or randomised.</p>
        <a class="read-more">Read More</a>
      </div>
    </div>
    <div class="center"><a class="btn">Parent Registration</a></div>
  </div>
</section>

<section class="logins">
  <div class="logins-photo" role="img" aria-label="Children learning together around a laptop, darkened background"></div>
  <div class="logins-shade"></div>
  <div class="wrap">
    <h2 class="section-title">Student Log-ins</h2>
    <form class="login-form">
      <div class="field">Name :</div>
      <div class="field">Email :</div>
      <div class="field">Course :</div>
      <div class="field">State :</div>
      <div class="field">Mobile :</div>
      <a class="btn">Student Log-ins</a>
    </form>
  </div>
</section>

<section class="services">
  <div class="wrap">
    <h2 class="section-title">Our Services</h2>
    <p class="section-lead">There are many variations of passages of Lorem Ipsum available, but the majority have suffered alteration in some form, by injected humour, or randomised words which don't look even slightly believable. If you are going to use a passage of Lorem Ipsum, you need</p>
    <div class="service-cards">
      <article class="service-card">
        <div class="service-photo" role="img" aria-label="Child's hand writing in a notebook with coloured pencils" style="background:linear-gradient(135deg,#d9cbbd,#f1e9e0 50%,#b89c86)"></div>
        <h3>Webcam and Within</h3>
        <p>We offer our clients prompt, professional and friendly service on all types of electrical projects, including new homes, remodels, and custom installations. Harlow Electric has been proudly serving Northern</p>
        <a class="btn">Read More</a>
      </article>
      <article class="service-card">
        <div class="service-photo" role="img" aria-label="Tutor helping a student with books at a desk" style="background:linear-gradient(135deg,#7a5a3e,#c9a47c 45%,#e3d2b6 70%,#8a6a4e)"></div>
        <h3>Undergraduates</h3>
        <p>We are licensed, bonded, insured and well-qualified to install your home charging station. We are committed to helping you take advantage of the latest in automotive technology. We can assist you in making</p>
        <a class="btn">Read More</a>
      </article>
      <article class="service-card">
        <div class="service-photo" role="img" aria-label="Girl and tutor reviewing work on a tablet" style="background:linear-gradient(135deg,#c2453f,#e7c1ad 45%,#f3e4da 70%,#b89a8a)"></div>
        <h3>Interviews &amp; Assessments</h3>
        <p>No project is too big or too small. Our goal is to stay ahead of all the changes in the electrical industry so that we always offer you the most current information and service. From start to finish, we will.</p>
        <a class="btn">Read More</a>
      </article>
    </div>
  </div>
</section>

<section class="how">
  <div class="wrap">
    <div class="video" role="img" aria-label="Video still of a tutor and boy working at a laptop"><span class="play"></span></div>
    <div class="how-copy">
      <h2>How It Works</h2>
      <p>There are many variations of passages of Lorem Ipsum available, but the majority have suffered alteration in some form, by injected humour, or randomised words which don't look even slightly believable. If you are going to use a passage of Lorem Ipsum, you needThere are many variations of passages of Lorem Ipsum available, but the majority have suffered alteration in some form, by injected humour, or randomised words which don't look even slightly believable. If you are going to use a passage of Lorem Ipsum, you need to be sure there isn't anything embarrassing hidden in the middle of text. All the Lorem Ipsum generators on the Internet tend to repeat.</p>
      <a class="btn">Tutor Profile</a>
    </div>
  </div>
</section>

<footer class="site-footer">
  <div class="wrap">
    <div class="subscribe">
      <h4>Subscribe Newsletter :</h4>
      <div class="field">Enter Your Email id:</div>
      <a class="btn">Subscribe Now</a>
    </div>
    <div class="footer-cols">
      <div class="footer-col col-links">
        <h5>Our Links</h5>
        <ul><li><i class="bullet"></i>Home</li><li><i class="bullet"></i>About us</li><li><i class="bullet"></i>Tutor Bio</li><li><i class="bullet"></i>Testimonials</li><li><i class="bullet"></i>Subscription</li></ul>
      </div>
      <div class="footer-col col-contact">
        <h5>Contact Us</h5>
        <ul>
          <li><svg width="14" height="12" viewBox="0 0 14 12"><path d="M1 4 q6-5 12 0v2h-3v-2h-6v2h-3z M2 7h10v5h-10z" fill="#e4e4e4"/></svg>(000) 415.208.3361 (Phone)</li>
          <li><svg width="14" height="12" viewBox="0 0 14 12"><rect x="3" y="0" width="8" height="4" fill="#e4e4e4"/><rect x="0" y="5" width="14" height="7" fill="#e4e4e4"/></svg>(000) 415.208.3370 (Fax)</li>
          <li><svg width="14" height="12" viewBox="0 0 14 12"><rect x="0.5" y="1.5" width="13" height="9" fill="none" stroke="#e4e4e4"/><path d="M1 2l6 5 6-5" fill="none" stroke="#e4e4e4"/></svg><u>www.Brivora.com</u></li>
          <li><svg width="14" height="14" viewBox="0 0 14 14"><path d="M7 1a4 4 0 0 1 4 4c0 3-4 8-4 8s-4-5-4-8a4 4 0 0 1 4-4z" fill="#e4e4e4"/><circle cx="7" cy="5" r="1.5" fill="#2e2e2e"/></svg># 12 Fernhill Road, Lindale</li>
        </ul>
      </div>
      <div class="footer-col col-info">
        <h5>Information</h5>
        <ul><li><i class="bullet"></i>Account</li><li><i class="bullet"></i>Checkout</li><li><i class="bullet"></i>Log in</li><li><i class="bullet"></i>Register</li><li><i class="bullet"></i>Cart (0)</li></ul>
      </div>
      <div class="footer-col col-follow">
        <h5>Follow Us</h5>
        <p>Perspiciatis unde omnis the istenatus oluptatem accusantium beatae vitae dicta sunt explicabo.</p>
        <div class="socials"><span></span><span></span><span></span><span></span><span></span></div>
      </div>
    </div>
  </div>
  <div class="copyright">© Copyright 2016 &nbsp;Brivora.com - All Rights Reserved</div>
</footer>

</body>
</html>
```